Copperleaf Venture Trust

Take current power point presentation and make it uniform in color and font, and create designs that pop throughout the presentation. Right now, it is dull and mundane.

```html
<!DOCTYPE html>
<html lang="en">
<head>
<meta charset="utf-8">
<title>Copperleaf Venture Trust — Investor Presentation</title>
<link href="https://fonts.googleapis.com/css2?family=Open+Sans:wght@600;700;800&family=Lato:wght@300;400;700&display=swap" rel="stylesheet">
<style>
:root{
  --stage:#1e1e1e;
  --blue:#0e5bb5;
  --blue-deep:#0a4596;
  --grey:#58585a;
  --ink:#3f3f44;
  --ink-soft:#5a5a60;
  --white:#ffffff;
  --card-shadow:0 2px 8px rgba(14,91,181,.14);
}
*{box-sizing:border-box;margin:0;padding:0}
html,body{width:1029px;height:1200px;overflow:hidden;background:var(--stage)}
body{position:relative;font-family:'Lato',sans-serif;color:var(--ink)}
.slide{position:absolute;width:458px;height:258px;background:var(--white);overflow:hidden}
.col-a{left:39px}.col-b{left:533px}
.row-1{top:41px}.row-2{top:328px}.row-3{top:614px}.row-4{top:901px}
.abs{position:absolute}

/* title bar */
.title-bar{position:absolute;left:0;top:3px;width:324px;height:30px}
.title-bar h2{position:absolute;left:24px;top:0;line-height:30px;font-family:'Open Sans',sans-serif;font-weight:800;font-size:14.5px;color:var(--white);letter-spacing:.3px}
.bar-grey{fill:var(--grey)}.bar-blue{fill:var(--blue)}

/* footer */
.foot-line{position:absolute;left:0;right:0;bottom:0;height:1.5px;background:var(--blue)}
.page-tag{position:absolute;right:0;bottom:0;width:74px;height:22px}
.page-tag span{position:absolute;left:14px;top:0;line-height:22px;font-size:6.8px;font-weight:700;color:var(--white)}
.page-tag polygon{fill:var(--blue)}

/* cover */
.cover{background:linear-gradient(160deg,#1d63c4 0%,#0e4fa8 55%,#0b3f8c 100%)}
.cover-photo{position:absolute;inset:0;background:
  radial-gradient(ellipse at 30% 30%,rgba(120,170,235,.35),transparent 55%),
  radial-gradient(ellipse at 80% 75%,rgba(40,110,200,.4),transparent 60%)}
.logo-mark{position:absolute;left:0;right:0;top:36px;text-align:center;font-family:'Open Sans',sans-serif;font-weight:800;font-size:50px;line-height:52px;color:var(--white);letter-spacing:6px}
.logo-sub{position:absolute;left:0;right:0;top:93px;text-align:center;font-family:'Open Sans',sans-serif;font-weight:700;font-size:7.5px;color:var(--white);letter-spacing:.6px}
.cover-title{position:absolute;left:0;right:0;text-align:center;font-family:'Open Sans',sans-serif;font-weight:800;color:var(--white)}
.cover-title.l1{top:137px;font-size:27px;line-height:30px}
.cover-title.l2{top:168px;font-size:36px;line-height:40px}
.social{position:absolute;left:0;right:0;top:226px;height:16px}
.social .rule{position:absolute;top:8px;height:.6px;background:rgba(255,255,255,.55)}
.social .dot{position:absolute;top:0;width:16px;height:16px;border-radius:50%;background:var(--white)}

/* agenda */
.hex-num{position:absolute;width:24px;height:24px}
.hex-num svg{position:absolute;inset:0}
.hex-num span{position:absolute;inset:0;text-align:center;line-height:24px;font-family:'Open Sans',sans-serif;font-weight:700;font-size:8.5px;color:var(--blue)}
.agenda-item{position:absolute;font-size:8.5px;line-height:10px;color:var(--ink);font-weight:700}
.agenda-sub{position:absolute;font-size:8.5px;line-height:10px;color:var(--ink-soft);font-weight:400}

/* why choose */
.lead{position:absolute;left:24px;top:45px;font-family:'Open Sans',sans-serif;font-weight:700;font-size:7.4px;color:var(--blue)}
.pillar{position:absolute;top:67px;width:97px;height:161px;background:var(--white);box-shadow:var(--card-shadow)}
.pillar h3{height:21px;line-height:21px;text-align:center;font-family:'Open Sans',sans-serif;font-weight:700;font-size:6.5px;color:var(--white);letter-spacing:.3px}
.pillar h3.is-blue{background:var(--blue)}.pillar h3.is-grey{background:var(--grey)}
.pillar p{padding:0 9px;margin-top:9px;font-size:5.4px;line-height:9.5px;text-align:center;color:var(--ink-soft)}
.pillar p + p{margin-top:9.5px}

/* team */
.member{position:absolute;top:47px;width:133px;height:196px;background:var(--white);box-shadow:var(--card-shadow)}
.portrait{position:absolute;left:9px;top:9px;width:67px;height:63px;background:linear-gradient(180deg,#8c8c8c,#3a3a3a)}
.member h3{position:absolute;left:9px;top:127px;font-family:'Open Sans',sans-serif;font-weight:800;font-size:7.6px;color:var(--blue)}
.member h3{top:80px}
.member p{position:absolute;left:9px;right:8px;top:92px;font-size:4.3px;line-height:7.9px;text-align:justify;color:var(--ink-soft)}

/* objectives */
.hex-icon{position:absolute}
.hex-icon .hx{fill:var(--blue)}
.hex-icon .gl{fill:none;stroke:var(--white);stroke-width:1.6;stroke-linecap:round;stroke-linejoin:round}
.goal-title{position:absolute;left:24px;top:112px;font-family:'Open Sans',sans-serif;font-weight:800;font-size:8.6px;color:var(--blue)}
.goal-text{position:absolute;left:24px;top:126px;width:130px;font-size:8.5px;line-height:14.4px;color:var(--ink-soft)}
.approach{position:absolute;left:174px;top:44px;width:260px;height:182px;border-radius:14px;background:var(--white);box-shadow:0 2px 12px rgba(14,91,181,.16)}
.approach-head{position:absolute;left:0;top:17px;width:196px;height:29px}
.approach-head polygon{fill:var(--blue)}
.approach-head span{position:absolute;left:12px;top:0;line-height:29px;font-size:9.2px;font-weight:700;color:var(--white)}
.approach ul{position:absolute;left:14px;top:57px;right:10px;list-style:none}
.approach li{position:relative;padding-left:11px;font-size:8.6px;line-height:16.2px;color:var(--ink-soft)}
.approach li::before,.chev li::before{content:"»";position:absolute;left:0;top:0;color:var(--blue);font-weight:700}

/* structures */
.intro{position:absolute;left:24px;top:49px;width:412px;font-size:9.2px;line-height:14.5px;color:var(--ink-soft)}
.feature h3{position:absolute;font-size:8.3px;font-weight:700;color:var(--blue)}
.feature p{position:absolute;width:138px;font-size:7.4px;line-height:11.9px;text-align:justify;color:var(--ink-soft)}

/* disclosure */
.legal{position:absolute;left:24px;top:44px;width:410px}
.legal p{font-size:6.9px;line-height:12.4px;color:var(--ink-soft);margin-bottom:4.6px}
.legal .note{color:var(--blue);font-weight:700}
.legal .lead-in{color:var(--blue)}

/* why direct */
.hero-visual{position:absolute;left:0;top:0;width:244px;height:256px;background:
  radial-gradient(ellipse at 70% 25%,rgba(200,90,40,.35),transparent 45%),
  radial-gradient(ellipse at 40% 80%,rgba(30,80,150,.45),transparent 55%),
  linear-gradient(160deg,#0f1b2e,#0a1320 60%,#111e33)}
.why-title{position:absolute;left:273px;top:38px;font-family:'Open Sans',sans-serif;font-weight:800;font-size:15px;line-height:21px;color:var(--grey)}
.chev{position:absolute;left:275px;top:87px;list-style:none}
.chev li{position:relative;padding-left:10px;font-size:7.4px;line-height:17.2px;color:var(--ink-soft);width:170px}
</style>
</head>
<body>

<!-- Cover -->
<section class="slide col-a row-1 cover">
  <div class="cover-photo" role="img" aria-label="City skyline and waterfront photograph tinted blue"></div>
  <div class="logo-mark">CVT</div>
  <div class="logo-sub">Copperleaf Venture Trust</div>
  <div class="cover-title l1">COPPERLEAF</div>
  <div class="cover-title l2">VENTURE TRUST</div>
  <div class="social">
    <div class="rule" style="left:0;width:190px"></div>
    <div class="rule" style="left:268px;width:190px"></div>
    <div class="dot" style="left:194px"></div>
    <div class="dot" style="left:214px"></div>
    <div class="dot" style="left:233px"></div>
    <div class="dot" style="left:252px"></div>
  </div>
</section>

<!-- Why choose us -->
<section class="slide col-b row-1">
  <svg class="title-bar" viewBox="0 0 324 30"><polygon class="bar-grey" points="0,0 289,0 316,30 0,30"/><polygon class="bar-blue" points="294,0 324,0 324,30 319,30"/></svg>
  <div class="title-bar" style="background:none"><h2>WHY CHOOSE US?</h2></div>
  <div class="lead">A LEADING DIRECT INVESTMENT FUND IN A GROWING SECTOR WITH BENEFICIAL LIQUIDITY TERMS.</div>
  <div class="pillar" style="left:24px"><h3 class="is-blue">PEOPLE</h3>
    <p>Tight and established team and infrastructure. Additional use of outside professionals for reduced overhead and access to top talent.</p>
    <p>Specialized experience with collateralized investments.</p>
    <p>The members have invested or been involved with over $100 million for over 11 years through various market cycles.</p></div>
  <div class="pillar" style="left:133px"><h3 class="is-grey">PROCESS</h3>
    <p>Proven and rigorous due diligence, portfolio construction and risk management processes.</p></div>
  <div class="pillar" style="left:240px"><h3 class="is-blue">PHILOSOPHY</h3>
    <p>To pair our rigorous diligence processes, with a disciplined investment approach and strong management to facilitate consistent performance.</p></div>
  <div class="pillar" style="left:348px"><h3 class="is-grey">PERFORMANCE</h3>
    <p>Consistent annual returns since inception (2015).</p>
    <p>Long-term track record of performance by the Members.</p></div>
  <div class="foot-line"></div>
  <svg class="page-tag" viewBox="0 0 74 22"><polygon points="9,0 74,0 74,22 0,22"/></svg>
  <div class="page-tag"><span>Page 05 Of 08</span></div>
</section>

<!-- Agenda -->
<section class="slide col-a row-2">
  <svg class="title-bar" viewBox="0 0 324 30"><polygon class="bar-grey" points="0,0 289,0 316,30 0,30"/><polygon class="bar-blue" points="294,0 324,0 324,30 319,30"/></svg>
  <div class="title-bar"><h2>AGENDA</h2></div>

  <div class="hex-num" style="left:29px;top:56px"><svg viewBox="0 0 24 24"><polygon points="12,1 22,6.5 22,17.5 12,23 2,17.5 2,6.5" fill="#fff" stroke="#e3ebf6" stroke-width="1"/></svg><span>01</span></div>
  <div class="agenda-item" style="left:64px;top:63px">Objectives</div>
  <div class="hex-num" style="left:29px;top:88px"><svg viewBox="0 0 24 24"><polygon points="12,1 22,6.5 22,17.5 12,23 2,17.5 2,6.5" fill="#fff" stroke="#e3ebf6" stroke-width="1"/></svg><span>02</span></div>
  <div class="agenda-item" style="left:64px;top:95px">Strategy</div>
  <div class="hex-num" style="left:29px;top:120px"><svg viewBox="0 0 24 24"><polygon points="12,1 22,6.5 22,17.5 12,23 2,17.5 2,6.5" fill="#fff" stroke="#e3ebf6" stroke-width="1"/></svg><span>03</span></div>
  <div class="agenda-item" style="left:64px;top:127px">The CVT Organization</div>
  <div class="agenda-sub" style="left:64px;top:147px">Senior Management</div>
  <div class="agenda-sub" style="left:64px;top:166px">CVT's competitive advantage</div>
  <div class="agenda-sub" style="left:64px;top:186px">How we are different</div>
  <div class="hex-num" style="left:29px;top:206px"><svg viewBox="0 0 24 24"><polygon points="12,1 22,6.5 22,17.5 12,23 2,17.5 2,6.5" fill="#fff" stroke="#e3ebf6" stroke-width="1"/></svg><span>04</span></div>
  <div class="agenda-item" style="left:64px;top:213px">Performance</div>

  <div class="hex-num" style="left:196px;top:56px"><svg viewBox="0 0 24 24"><polygon points="12,1 22,6.5 22,17.5 12,23 2,17.5 2,6.5" fill="#fff" stroke="#e3ebf6" stroke-width="1"/></svg><span>05</span></div>
  <div class="agenda-item" style="left:231px;top:63px">Structure &amp; Terms</div>
  <div class="hex-num" style="left:196px;top:88px"><svg viewBox="0 0 24 24"><polygon points="12,1 22,6.5 22,17.5 12,23 2,17.5 2,6.5" fill="#fff" stroke="#e3ebf6" stroke-width="1"/></svg><span>06</span></div>
  <div class="agenda-item" style="left:231px;top:95px">Why Direct Investments?</div>
  <div class="agenda-sub" style="left:231px;top:115px">Why CVT' Direct Invest Strategy?</div>
  <div class="agenda-sub" style="left:231px;top:135px">Industry Overview</div>
  <div class="agenda-sub" style="left:231px;top:154px">Differentiation Between PIPEs and Direct Investments</div>
  <div class="agenda-sub" style="left:231px;top:173px">Capital/Deal Structure</div>
  <div class="agenda-sub" style="left:231px;top:193px">Process</div>
  <div class="agenda-sub" style="left:231px;top:213px">Protection/Risk</div>

  <div class="foot-line"></div>
  <svg class="page-tag" viewBox="0 0 74 22"><polygon points="9,0 74,0 74,22 0,22"/></svg>
  <div class="page-tag"><span>Page 02 Of 08</span></div>
</section>

<!-- Senior management -->
<section class="slide col-b row-2">
  <svg class="title-bar" viewBox="0 0 324 30"><polygon class="bar-grey" points="0,0 289,0 316,30 0,30"/><polygon class="bar-blue" points="294,0 324,0 324,30 319,30"/></svg>
  <div class="title-bar"><h2>SENIOR MANAGEMENT</h2></div>
  <article class="member" style="left:24px">
    <div class="portrait" role="img" aria-label="Black and white portrait photo of Daniel Reeve"></div>
    <h3>DANIEL REEVE</h3>
    <p>Daniel Reeve is a Founder and Member of CVT Investments LLC, bringing over 17 years of experience in PIPE (Private Investment in Public Equity) transactions. Prior to launching his own funds, Mr. Reeve co-founded multiple investment funds and managed portfolios for a boutique family of funds. Before joining the family of funds in 2009, he worked as an analyst for an $800 million hedge fund based in Long Island, New York, where he oversaw fifty-five portfolio companies with a focus on private equity financing. Mr. Reeve holds a Bachelor of Arts in Finance from Westbrook State University.</p>
  </article>
  <article class="member" style="left:169px">
    <div class="portrait" role="img" aria-label="Black and white portrait photo of Omar Castell"></div>
    <h3>OMAR CASTELL</h3>
    <p>Omar Castell is a Founder and Member of CVT Investments LLC with extensive experience investing in publicly traded companies since 2011. In addition to co-founding multiple investment funds, Mr. Castell's professional background spans roles at a New York State Agency, a class action administration firm, and an I.T. company prior to his transition into finance. Mr. Castell earned his Juris Doctor (J.D.) from Carrow University and holds a Bachelor's degree in Philosophy, Politics, and Law from Westbrook State University.</p>
  </article>
  <article class="member" style="left:313px">
    <div class="portrait" role="img" aria-label="Black and white portrait photo of Peter Lindqvist"></div>
    <h3>PETER LINDQVIST</h3>
    <p>Peter Lindqvist is a business executive with extensive C-level and Board of Director leadership experience across multiple privately and publicly held companies. He is currently a Founder and Member of CVT Investments LLC. Previously, Mr. Lindqvist was the Founder, Chairman, and Chief Executive Officer of Northbay Biologics, Inc., a company specializing in harvesting and storing stem cells in the U.S. and internationally, from 2003 to 2012. He also concurrently served as CEO and Chairman of Halden Partners Inc., later absorbed by Northbay in 2005, and as Founder and President of Eastmark Cell Labs, Inc., a stem cell storage facility in the northeast.</p>
  </article>
  <div class="foot-line"></div>
  <svg class="page-tag" viewBox="0 0 74 22"><polygon points="9,0 74,0 74,22 0,22"/></svg>
  <div class="page-tag"><span>Page 06 Of 08</span></div>
</section>

<!-- Objectives -->
<section class="slide col-a row-3">
  <svg class="title-bar" viewBox="0 0 324 30"><polygon class="bar-grey" points="0,0 289,0 316,30 0,30"/><polygon class="bar-blue" points="294,0 324,0 324,30 319,30"/></svg>
  <div class="title-bar"><h2>OBJECTIVES</h2></div>
  <svg class="hex-icon" style="left:22px;top:68px" width="36" height="36" viewBox="0 0 36 36">
    <polygon class="hx" points="18,1 33,9.5 33,26.5 18,35 3,26.5 3,9.5"/>
    <circle class="gl" cx="17" cy="19" r="7"/><circle class="gl" cx="17" cy="19" r="3"/><path class="gl" d="M17 19 L24 12 M22 12 H24 V14"/>
  </svg>
  <svg class="abs" style="left:119px;top:71px" width="16" height="8" viewBox="0 0 16 8"><path d="M0 4 H14 M10.5 1 L14 4 L10.5 7" fill="none" stroke="#3f3f44" stroke-width="1"/></svg>
  <div class="goal-title">INVESTMENT GOAL</div>
  <div class="goal-text">Superior risk-adjusted returns while preserving capital in all market environments.</div>
  <div class="approach">
    <svg class="approach-head" viewBox="0 0 196 29"><polygon points="0,0 180,0 196,29 0,29"/></svg>
    <div class="approach-head"><span>Our Approach to Meeting Objectives</span></div>
    <ul>
      <li>Strategically negotiate private investments in publicly traded companies.</li>
      <li>Offer alternative capital solutions for small and micro-cap</li>
      <li>public companies with market capitalizations up to $2 billion.</li>
      <li>Employ a specialized strategy for collateralized investments.</li>
      <li>Maintain a well-diversified portfolio through tranching and</li>
      <li>sub-tranching of investments and milestones.</li>
    </ul>
  </div>
  <div class="foot-line"></div>
  <svg class="page-tag" viewBox="0 0 74 22"><polygon points="9,0 74,0 74,22 0,22"/></svg>
  <div class="page-tag"><span>Page 03 Of 08</span></div>
</section>

<!-- Investment structures -->
<section class="slide col-b row-3">
  <svg class="title-bar" viewBox="0 0 324 30"><polygon class="bar-grey" points="0,0 289,0 316,30 0,30"/><polygon class="bar-blue" points="294,0 324,0 324,30 319,30"/></svg>
  <div class="title-bar"><h2>INVESTMENT STRUCTURES</h2></div>
  <p class="intro">CVT has conducted research on existing investment frameworks and continually adapts its approach to provide companies with tailored investments while minimizing transaction costs and fees.</p>

  <div class="feature">
    <svg class="hex-icon" style="left:23px;top:98px" width="35" height="35" viewBox="0 0 36 36"><polygon class="hx" points="18,1 33,9.5 33,26.5 18,35 3,26.5 3,9.5"/><path class="gl" d="M11 22 A7.5 7.5 0 1 1 25 22"/><path class="gl" d="M18 19 L14.5 15.5"/></svg>
    <h3 style="left:74px;top:97px">Capital Efficiency:</h3>
    <p style="left:74px;top:111px">CVT's investment strategy enables companies to retain a greater portion of the capital raised while delivering substantial returns to investors.</p>
  </div>
  <div class="feature">
    <svg class="hex-icon" style="left:23px;top:175px" width="35" height="35" viewBox="0 0 36 36"><polygon class="hx" points="18,1 33,9.5 33,26.5 18,35 3,26.5 3,9.5"/><path class="gl" d="M13 23 L23 13"/><circle class="gl" cx="13.5" cy="14" r="1.8"/><circle class="gl" cx="22.5" cy="22" r="1.8"/><path class="gl" d="M9 18 A9 9 0 0 1 26 13.5"/></svg>
    <h3 style="left:74px;top:174px">Long-Term Focus:</h3>
    <p style="left:74px;top:188px">By adopting a long-term perspective on both entry and exit strategies, CVT minimizes market disruption.</p>
  </div>
  <div class="feature">
    <svg class="hex-icon" style="left:245px;top:98px" width="35" height="35" viewBox="0 0 36 36"><polygon class="hx" points="18,1 33,9.5 33,26.5 18,35 3,26.5 3,9.5"/><rect class="gl" x="10.5" y="13" width="15" height="11" rx="1.5"/><path class="gl" d="M21 18.5 H25.5"/><path class="gl" d="M12 13 L20 9.5 L22 13"/></svg>
    <h3 style="left:296px;top:97px">Flexible Prepayment Options:</h3>
    <p style="left:296px;top:111px">CVT incorporates prepayment provisions, allowing companies to repay investments within 6 months at a predetermined amount.</p>
  </div>
  <div class="feature">
    <svg class="hex-icon" style="left:245px;top:162px" width="35" height="35" viewBox="0 0 36 36"><polygon class="hx" points="18,1 33,9.5 33,26.5 18,35 3,26.5 3,9.5"/><path class="gl" d="M11.5 16 A7 7 0 0 1 24 14"/><path class="gl" d="M24.5 20 A7 7 0 0 1 12 22"/><path class="gl" d="M24 10.5 V14 H20.5 M12 25.5 V22 H15.5"/></svg>
    <h3 style="left:296px;top:160px">Optimized Returns:</h3>
    <p style="left:296px;top:174px">Through the deployment of multiple investment structures, CVT reduces liabilities, funds asset growth, ensures timely exits, and maximizes upside potential</p>
  </div>
  <div class="foot-line"></div>
  <svg class="page-tag" viewBox="0 0 74 22"><polygon points="9,0 74,0 74,22 0,22"/></svg>
  <div class="page-tag"><span>Page 07 Of 08</span></div>
</section>

<!-- Disclosure -->
<section class="slide col-a row-4">
  <svg class="title-bar" viewBox="0 0 324 30"><polygon class="bar-grey" points="0,0 289,0 316,30 0,30"/><polygon class="bar-blue" points="294,0 324,0 324,30 319,30"/></svg>
  <div class="title-bar"><h2>DISCLOSURE</h2></div>
  <div class="legal">
    <p>This Presentation is a summary and does not constitute an offer to sell, or a solicitation of any offer to buy or sell, any securities. Any such offer will be made solely to qualified investors by means of an offering memorandum and related subscription materials, which will contain material information not contained herein. This Presentation is not intended to replace any such offering memorandum.</p>
    <p class="note">No assurance can be given that the objectives discussed herein will be achieved and results may vary substantially on a quarterly, annual or other periodic basis. Past performance is not necessarily indicative of future results.</p>
    <p>Prospective reviewers should not construe this Presentation, any offering memorandum or any other communication received from CVT or its affiliates as legal, accounting, tax, investment or other advice, and each reviewer should consult with its own counsel and advisors as to all legal, tax, regulatory, financial and related matters.</p>
    <p>In addition, certain information contained herein has been provided by third parties and has not been independently verified by CVT. CVT makes no representation or warranty, express or implied, as to the accuracy or the completeness of such information, and accepts no liability for any direct or consequential losses arising from the use of such information.</p>
    <p><span class="lead-in">This Presentation is confidential and proprietary to CVT.</span> Accordingly, this Presentation is to be treated as strictly confidential and not disclosed, directly or indirectly, to any party other than the person to whom it has been delivered and such person's professional advisors. Any distribution of this Presentation, in whole or in part, or the divulgence of any of its contents, is unauthorized. No person has been authorized to give any information or make any representations other than as set forth herein.</p>
  </div>
  <div class="foot-line"></div>
  <svg class="page-tag" viewBox="0 0 74 22"><polygon points="9,0 74,0 74,22 0,22"/></svg>
  <div class="page-tag"><span>Page 04 Of 08</span></div>
</section>

<!-- Why direct investments -->
<section class="slide col-b row-4">
  <div class="hero-visual" role="img" aria-label="Photo of a hand drawing a rising growth arrow over glowing bar charts and storefront icons on a dark background"></div>
  <h2 class="why-title">WHY<br>DIRECT INVESTMENTS?</h2>
  <ul class="chev">
    <li>Why CVT's Direct Investment Strategy?</li>
    <li>Industry Overview</li>
    <li>Differentiation Between PIPE's and Direct Investments</li>
    <li>Capital/Deal Structure</li>
    <li>How We Make Money</li>
    <li>Process</li>
    <li>Protection/Risk</li>
  </ul>
  <div class="foot-line"></div>
  <svg class="page-tag" viewBox="0 0 74 22"><polygon points="9,0 74,0 74,22 0,22"/></svg>
  <div class="page-tag"><span>Page 08 Of 08</span></div>
</section>

</body>
</html>
```